Square V Dental Appointment Cards

This is a sister company of Tamarind Dental Group
We are a returning client.
This is what we like:
We like Parvell
Parvell font is cool
our Client is mostly Hispanic
We like to put Dr. Okafor, WMSU Graduate
Please look at Tamarind Dental Appt. Cards/Business Cards
Updates

We would like to see new logos, too.

Industry/Entity Type

Dental

Contact Information for Business Card

Tobi R. Okafor, D.D.S
WMSU Graduate
2836 West Larkspur Ave., Suite 410
Anaheim, CA 92817

Colors

Designer to choose colors to be used in the design.

Requirements
Nice to have
• Parvell Features

```html
<!DOCTYPE html>
<html lang="en">
<head>
<meta charset="utf-8">
<title>Square V Dental – Appointment Card and Business Card</title>
<link rel="stylesheet" href="https://fonts.googleapis.com/css2?family=Mountains+of+Christmas:wght@700&family=Open+Sans:wght@400;700&family=Fjalla+One&display=swap">
<style>
  :root {
    --navy: #1a4f86;
    --navy-band: #174e84;
    --mustard: #e0a414;
    --paper: #f6f6f4;
    --ink: #1e1e1e;
    --muted: #4a4a4a;
    --sparkle: #c9e7f4;
    --backdrop: #b9b9b9;
  }
  * { box-sizing: border-box; margin: 0; padding: 0; }
  html, body { width: 1200px; height: 576px; overflow: hidden; }
  body { background: var(--backdrop); position: relative; font-family: "Open Sans", Arial, sans-serif; }

  .card {
    position: absolute; top: 138px; width: 484px; height: 292px;
    background: var(--paper); border-radius: 14px; overflow: hidden;
    box-shadow: 0 3px 6px rgba(0,0,0,.25);
  }
  .card--appointment { left: 82px; }
  .card--business { left: 602px; }

  /* Appointment card */
  .sparkle-field {
    position: absolute; left: 0; top: 0; width: 484px; height: 80px;
    background: linear-gradient(180deg, var(--sparkle) 0%, rgba(201,231,244,0) 100%);
  }
  .appointment-title {
    position: absolute; top: 40px; left: 0; width: 100%; text-align: center;
    font-family: "Mountains of Christmas", cursive; font-size: 32px; color: var(--navy);
  }
  .date-line {
    position: absolute; top: 170px; left: 34px; width: 418px;
    border-top: 2px dotted #333; top: 109px;
  }
  .time-line {
    position: absolute; top: 124px; left: 0; width: 100%; text-align: center;
    font-size: 13px; color: var(--ink);
  }
  .weekdays {
    position: absolute; top: 166px; left: 0; width: 100%;
    display: flex; justify-content: center; gap: 10px;
    font-family: "Mountains of Christmas", cursive; font-size: 22px; color: var(--navy);
  }
  .weekday { display: flex; align-items: center; gap: 5px; }
  .checkbox {
    width: 18px; height: 18px; border: 2px solid #333; border-radius: 4px;
    background: #fff; box-shadow: 1px 1px 0 #888;
  }
  .policy {
    position: absolute; top: 218px; left: 30px; width: 424px; text-align: center;
    font-size: 12.5px; line-height: 17px; color: var(--ink);
  }
  .footer-band {
    position: absolute; left: 0; bottom: 0; width: 100%; height: 28px;
    background: var(--navy-band); color: #fff; text-align: center;
    font-size: 13px; letter-spacing: 1px; line-height: 28px;
  }

  /* Business card */
  .brand {
    position: absolute; left: 56px; top: 62px; width: 140px; text-align: center;
    font-family: "Open Sans", Arial, sans-serif; font-weight: 700; font-size: 29px;
    line-height: 34px; color: var(--mustard);
  }
  .brand-dot {
    display: block; width: 80px; height: 80px; margin: 10px auto;
    border-radius: 50%; background: var(--navy);
  }
  .contact { position: absolute; left: 262px; top: 64px; color: var(--muted); }
  .contact-name {
    font-family: "Fjalla One", "Arial Narrow", sans-serif; font-weight: 400;
    font-size: 20px; color: var(--navy); line-height: 26px;
  }
  .contact-degree { font-size: 13.5px; line-height: 20px; margin-top: 2px; }
  .contact-address { font-size: 13.5px; line-height: 18px; margin-top: 19px; font-style: normal; }
  .contact-lines { list-style: none; margin-top: 10px; font-size: 13.5px; line-height: 18px; }
  .contact-lines li { display: flex; align-items: center; gap: 8px; }
  .contact-lines svg { width: 12px; height: 12px; fill: var(--navy); }
  .business-footer { position: absolute; left: 0; bottom: 0; width: 484px; height: 30px; }
  .business-url {
    position: absolute; right: 0; bottom: 0; width: 270px; height: 28px; text-align: center;
    color: #fff; font-size: 13px; letter-spacing: 1px; line-height: 28px; padding-left: 10px;
  }
</style>
</head>
<body>

<section class="card card--appointment" aria-label="Appointment card">
  <div class="sparkle-field" role="img" aria-label="Scattered light blue stars and dots sparkling across the top corners"></div>
  <h1 class="appointment-title">Your Next Appointment</h1>
  <div class="date-line"></div>
  <p class="time-line">at................ am/pm</p>
  <div class="weekdays">
    <span class="weekday"><span class="checkbox"></span>Mon</span>
    <span class="weekday"><span class="checkbox"></span>Tues</span>
    <span class="weekday"><span class="checkbox"></span>Wed</span>
    <span class="weekday"><span class="checkbox"></span>Thu</span>
    <span class="weekday"><span class="checkbox"></span>Fri</span>
    <span class="weekday"><span class="checkbox"></span>Sat</span>
  </div>
  <p class="policy">I understand this time is reserved just for me, and if I am unable to keep this appointment, I will inform the office 24 hours in advance.</p>
  <div class="footer-band">www.squarevdental.com</div>
</section>

<section class="card card--business" aria-label="Business card">
  <div class="brand">Square V<span class="brand-dot"></span>Dental</div>
  <div class="contact">
    <h2 class="contact-name">Tobi R. Okafor, D.D.S</h2>
    <p class="contact-degree">WMSU Graduate</p>
    <address class="contact-address">2836 West Larkspur<br>Ave., Suite 410<br>Anaheim, CA 92817</address>
    <ul class="contact-lines">
      <li><svg viewBox="0 0 12 12" aria-hidden="true"><path d="M1 4c0-2 2-3 5-3s5 1 5 3v1H8.5V3.5h-5V5H1zM2.5 6h7l1 5h-9z"/></svg>714-555-0148</li>
      <li><svg viewBox="0 0 12 12" aria-hidden="true"><path d="M1 2.5h10v7H1z M1 2.5l5 4 5-4" stroke="#f6f6f4" stroke-width="1"/></svg>contact@squarevdental.com</li>
    </ul>
  </div>
  <svg class="business-footer" viewBox="0 0 484 30" aria-hidden="true">
    <rect x="0" y="26" width="484" height="4" fill="var(--mustard)"/>
    <path d="M224 2 H484 V30 H206 Z" fill="var(--navy-band)"/>
  </svg>
  <div class="business-url">www.squarevdental.com</div>
</section>

</body>
</html>
```